Brell Stone Company Business Cards

Front and Back Business Card - logo and text setup - cool design. I need workable photoshop or illustrator files so I can setup each employee card with design that is created
Updates

Hi everyone, thank you for the great entries. Please no more white and blue cards - there are so many already - black and silver only now please. thanks!

Target Market(s)

Construction Industry - Facility Managers

Industry/Entity Type

Construction

Contact Information for Business Card

I really like contemporary simplistic looks - clean neat....not opposed to seeing some black backrounds

Requirements
Must have
• Logo/website address with design on front only - www.brellstone-example.com (logo attached)
• Back:
• Name/Title/Company Address/Phone/email address
Nice to have
• Cool design
Should not have
• Nothing gimmicky like Fire or Water - since we are a Fire Protection company - it has all been done

```html
<!DOCTYPE html>
<html lang="en">
<head>
<meta charset="utf-8">
<title>Brell Stone Company Business Cards</title>
<link rel="stylesheet" href="https://fonts.googleapis.com/css2?family=Open+Sans:wght@400;700;800&display=swap">
<style>
  :root {
    --backdrop: #c9ccce;
    --card-black: #000000;
    --brand-blue: #0323a0;
    --brand-red: #ff2222;
    --icon-red: #f0452e;
    --text-white: #ffffff;
  }
  * { margin: 0; padding: 0; box-sizing: border-box; }
  html, body { width: 1200px; height: 1193px; overflow: hidden; }
  body {
    position: relative;
    background: var(--backdrop);
    font-family: "Open Sans", Arial, sans-serif;
    color: var(--text-white);
  }
  .card {
    position: absolute;
    width: 872px;
    height: 499px;
    border-radius: 42px;
    overflow: hidden;
  }
  .card-contact { left: 284px; top: 70px; background: var(--card-black); }
  .card-brand { left: 60px; top: 623px; background: var(--brand-red); }

  .wave { position: absolute; inset: 0; width: 872px; height: 499px; }

  .contact-wordmark {
    position: absolute;
    left: 94px; top: 40px;
    font-weight: 800;
    font-size: 74px;
    line-height: 1;
    letter-spacing: -1px;
    color: var(--brand-blue);
  }
  .contact-list { position: absolute; left: 88px; top: 206px; list-style: none; }
  .contact-item {
    display: flex; align-items: center;
    height: 38.5px;
    font-size: 22px;
  }
  .contact-item svg { width: 22px; height: 22px; margin-right: 11px; flex: none; }
  .address {
    position: absolute; left: 88px; top: 331px;
    font-size: 22px; line-height: 33px;
  }
  .person {
    position: absolute; left: 613px; top: 382px; width: 200px;
    text-align: center; white-space: nowrap;
  }
  .person-name { font-weight: 700; font-size: 33px; line-height: 42px; }
  .person-title { font-size: 31px; line-height: 42px; }

  .brand-wordmark {
    position: absolute; left: 0; right: 0; top: 150px;
    text-align: center;
    font-weight: 800;
    font-size: 104px;
    line-height: 1;
    letter-spacing: -2px;
    color: var(--text-white);
  }
  .brand-url {
    position: absolute; left: 0; right: 0; top: 330px;
    text-align: center;
    font-size: 24px;
    letter-spacing: 6px;
  }
</style>
</head>
<body>
  <section class="card card-contact">
    <svg class="wave" viewBox="0 0 872 499" aria-hidden="true">
      <path d="M0 325 C40 420 120 458 210 455 C390 448 570 330 720 300 C800 285 845 305 872 355 L872 499 L0 499 Z" fill="var(--brand-blue)"/>
      <path d="M230 452 C420 425 590 320 740 298 C805 290 845 300 872 330" fill="none" stroke="var(--brand-blue)" stroke-width="10"/>
      <path d="M48 438 C120 492 300 482 480 412 C640 350 760 305 868 330" fill="none" stroke="var(--card-black)" stroke-width="6"/>
    </svg>

    <div class="contact-wordmark">Brell Stone</div>

    <ul class="contact-list">
      <li class="contact-item">
        <svg viewBox="0 0 24 24" aria-hidden="true"><path fill="var(--icon-red)" d="M6.6 2.5l3 3.6-1.8 2.2c1.3 2.9 3.6 5.3 6.5 6.7l2.3-1.8 3.6 3-2 3.3C10.500 19.600 4.200 13.200 3.300 4.400z"/></svg>
        <span>(555) 014-2290</span>
      </li>
      <li class="contact-item">
        <svg viewBox="0 0 24 24" aria-hidden="true"><rect x="1" y="5" width="22" height="14" fill="var(--icon-red)"/><path d="M1 5l11 8 11-8M1 19l8-7M23 19l-8-7" fill="none" stroke="var(--card-black)" stroke-width="1.6"/></svg>
        <span>info@brellstone-example.com</span>
      </li>
      <li class="contact-item">
        <svg viewBox="0 0 24 24" aria-hidden="true"><g fill="none" stroke="var(--icon-red)" stroke-width="1.6"><circle cx="12" cy="12" r="10"/><ellipse cx="12" cy="12" rx="4.5" ry="10"/><path d="M2 12h20M4 7h16M4 17h16"/></g></svg>
        <span>www.brellstone-example.com</span>
      </li>
    </ul>

    <p class="address">48 Harbor Park Road<br>Millbrook, NY 10592</p>

    <div class="person">
      <p class="person-name">Dana Whitfield</p>
      <p class="person-title">President</p>
    </div>
  </section>

  <section class="card card-brand">
    <div class="brand-wordmark">Brell Stone</div>
    <p class="brand-url">www.brellstone-example.com</p>
  </section>
</body>
</html>
```